Natural Light/Organic/Documentary Photography Business

I like a simple, approachable, feminine, earthy/organic feel. Earth/neutral tones, nothing too loud or obnoxious. I like the watercolor look. I don't want anything too trendy or something I'll get tired of after a couple months. As far as colors, I am much more a fan of cream/taupe/blue/green...not a fan of pink or purple at all.

Target Market(s)

Weddings & Families

Industry/Entity Type

Wedding Photography

Contact Information for Business Card

website, email, phone number

Font styles to use
Other font styles liked:
• Horizontes, Gotham

Colors

Designer to choose colors to be used in the design.

Requirements
Must have
• Website: www.mirelhatchway.com
• Phone: 418.629.5073
• Email: mirel@mirelhatchway.com
Nice to have
• I like the watercolor look but its not necessary. I like simple/earthy tones. Nothing too loud or distracting. Simple & feminine without being too girly. I like an approachable/soft feel.
• Instagram: www.instagram.com/mirelhatchwayphotography/
Should not have
• NO loud colors or design or pattern. I do not want a photo of a camera or lens or anything cheesy like that.

```html
<!DOCTYPE html>
<html lang="en">
<head>
<meta charset="utf-8">
<title>Mirel Hatchway Photography – Business Card</title>
<link rel="stylesheet" href="https://fonts.googleapis.com/css2?family=Mrs+Saint+Delafield&family=Montserrat:wght@400&family=Spectral+SC:wght@300;400&display=swap">
<style>
  :root {
    --paper: #fbfbfc;
    --ink: #111111;
    --ink-soft: #3a3b38;
    --wash-mist: #e9ece4;
    --wash-sage: #d9e0c8;
    --wash-lime: #eef3c4;
  }
  html, body {
    margin: 0;
    padding: 0;
    overflow: hidden;
    background: var(--paper);
  }
  .card {
    position: relative;
    width: 1200px;
    height: 678px;
    overflow: hidden;
    background: var(--paper);
  }
  .watercolor-wash {
    position: absolute;
    left: 140px;
    top: 96px;
    width: 950px;
    height: 520px;
    border-radius: 46% 50% 44% 52% / 42% 40% 58% 56%;
    background: linear-gradient(100deg, var(--wash-mist) 0%, var(--wash-lime) 50%, var(--wash-sage) 100%);
  }
  .brand {
    position: absolute;
    left: 0;
    right: 0;
    top: 150px;
    text-align: center;
    color: var(--ink);
  }
  .brand-name {
    margin: 0;
    font-family: "Mrs Saint Delafield", cursive;
    font-size: 132px;
    line-height: 130px;
    font-weight: 400;
    letter-spacing: 0.02em;
    padding-right: 20px;
  }
  .brand-tagline {
    margin: -6px 0 0;
    font-family: "Montserrat", Arial, sans-serif;
    font-size: 17px;
    font-weight: 400;
    letter-spacing: 0.72em;
    padding-left: 0.72em;
  }
  .contact-list {
    position: absolute;
    left: 0;
    right: 0;
    top: 356px;
    margin: 0;
    padding: 0;
    list-style: none;
    text-align: center;
    color: var(--ink-soft);
    font-family: "Spectral SC", Georgia, serif;
    font-size: 17px;
    font-weight: 300;
  }
  .contact-item {
    height: 50px;
    line-height: 26px;
  }
</style>
</head>
<body>
  <main class="card">
    <div class="watercolor-wash" role="img" aria-label="Soft sage and pale lime watercolour wash behind the name and contact details"></div>

    <header class="brand">
      <h1 class="brand-name">Mirel Hatchway</h1>
      <p class="brand-tagline">PHOTOGRAPHY</p>
    </header>

    <ul class="contact-list">
      <li class="contact-item">Cell: 418.629.5073</li>
      <li class="contact-item">Email: mirel@mirelhatchway.com</li>
      <li class="contact-item">Web: www. mirelhatchway.com</li>
      <li class="contact-item">Insta: @mirelhatchwayphotography</li>
    </ul>
  </main>
</body>
</html>
```